Keystonery Billboard - Financial Services Company (Investments, Tax Planning and Insurance)

Our new office has a billboard directly above the office building. We'd like something eye-catching with a strong Call to Action, with the main part of the billboard being under 7 words if possible. We'd like you to include a way to get ahold of us (either our website keystoneryllc.example or our phone number 302-418-2907. You may also include in small font something to indicate that we've been serving the area since 1980 (the DE area, the tri-state area, the Marlowe Hollow, etc.)

We offer financial planning, tax planning, and insurance, and we help our clients to focus on their goals and happiness by providing everything they need for lifelong wealth under one roof.

Our logos are attached, we use a triangle logo with green and gray. We use the tagline "discover lasting prosperity" but this does not need to be included.

Potential ideas we have seen from other financial companies-
- the concept that the driver spends more time looking at billboards than planning for their retirement
-something along the lines of "everything you need for your finances is in this building right here" planning, investments, taxes, insurance"
-don't spend your time worrying about retirement, let us help you plan for it
-are you working for your money, or is it working for you?
- retirement takes planning, we're here to help
- ready to retire? talk to us
- need investment advice?
- need help investing?
- crossing your fingers isn't a retirement plan. we can help.
- retiring soon? you need help.

Those are just general ideas, please feel free to be creative.

brand colors:
#00b585
#00b185
#000000
#ffffff
#6d6f75
#6d6f75
#6f7074
#021712
#052e24

```html
<!DOCTYPE html>
<html lang="en">
<head>
<meta charset="UTF-8">
<title>Keystonery Billboard</title>
<link href="https://fonts.googleapis.com/css2?family=Oswald:wght@600&family=Poppins:wght@500;600;700;800&display=swap" rel="stylesheet">
<style>
  :root {
    --page: #ffffff;
    --charcoal: #2b2b2c;
    --headline-gray: #8e8f93;
    --bar-gray: #6d6f75;
    --green: #00a56f;
    --green-light: #00b585;
    --green-deep: #052e24;
    --ink: #1f1f20;
    --white: #ffffff;
    --photo-warm: #e6e1da;
    --photo-cool: #f2f2f0;
  }
  * { margin: 0; padding: 0; box-sizing: border-box; }
  html, body {
    width: 1117px;
    height: 1200px;
    overflow: hidden;
    background: var(--page);
  }
  .canvas {
    position: relative;
    width: 1117px;
    height: 1200px;
  }
  .billboard {
    position: absolute;
    left: 66px;
    top: 457px;
    width: 984px;
    height: 285px;
    box-shadow: 0 10px 24px rgba(0, 0, 0, 0.22);
  }
  .billboard svg { display: block; }
  .headline { font-family: "Poppins", sans-serif; font-weight: 800; }
  .headline--lead { fill: var(--headline-gray); }
  .headline--main { fill: var(--white); }
  .brand-name { font-family: "Poppins", sans-serif; font-weight: 600; fill: var(--green); }
  .brand-tagline { font-family: "Poppins", sans-serif; font-weight: 500; fill: var(--bar-gray); letter-spacing: 2.6px; }
  .service { font-family: "Poppins", sans-serif; font-weight: 500; fill: var(--ink); }
  .cta { font-family: "Poppins", sans-serif; font-weight: 800; fill: var(--white); }
  .badge-text { font-family: "Poppins", sans-serif; font-weight: 700; fill: var(--white); }
  .badge-year { font-family: "Oswald", sans-serif; font-weight: 600; fill: var(--green-deep); }
</style>
</head>
<body>
<main class="canvas">
  <section class="billboard" aria-label="Keystonery billboard">
    <svg width="984" height="285" viewBox="0 0 984 285" xmlns="http://www.w3.org/2000/svg">
      <defs>
        <linearGradient id="photoTone" x1="0" y1="0" x2="0" y2="1">
          <stop offset="0" stop-color="var(--photo-cool)"/>
          <stop offset="0.7" stop-color="#ebe9e6"/>
          <stop offset="1" stop-color="var(--photo-warm)"/>
        </linearGradient>
        <radialGradient id="badgeTone" cx="0.45" cy="0.4" r="0.65">
          <stop offset="0" stop-color="var(--green-light)"/>
          <stop offset="1" stop-color="#008a5c"/>
        </radialGradient>
      </defs>

      <!-- backgrounds -->
      <rect class="panel-white" x="0" y="0" width="984" height="285" fill="var(--white)"/>
      <rect class="panel-dark" x="0" y="0" width="984" height="149" fill="var(--charcoal)"/>

      <!-- call to action bar -->
      <rect class="cta-bar-gray" x="240" y="229" width="440" height="44" fill="var(--bar-gray)"/>
      <rect class="cta-bar-green" x="0" y="229" width="256" height="44" fill="var(--green)"/>

      <!-- accent stripe and photo -->
      <polygon class="accent-stripe" points="821,0 860,0 694,285 652,285" fill="var(--green)"/>
      <g role="img" aria-label="Photo of a smiling young family sitting together on a light floor, the mother pointing upward">
        <polygon class="photo-area" points="860,0 984,0 984,285 694,285" fill="url(#photoTone)"/>
      </g>

      <!-- headline -->
      <text class="headline headline--lead" x="32" y="85" font-size="72" textLength="560" lengthAdjust="spacingAndGlyphs">WE INVEST IN</text>
      <text class="headline headline--main" x="32" y="146" font-size="72" textLength="644" lengthAdjust="spacingAndGlyphs">YOUR HAPPINESS</text>

      <!-- brand -->
      <rect class="brand-mark" x="31" y="181" width="18" height="18" fill="var(--green)"/>
      <text class="brand-name" x="55" y="199" font-size="25" textLength="150" lengthAdjust="spacingAndGlyphs">Keystonery</text>
      <text class="brand-tagline" x="56" y="210" font-size="6.4" textLength="150" lengthAdjust="spacing">DISCOVER LASTING PROSPERITY</text>

      <!-- services -->
      <g class="service-list">
        <g class="service-item" transform="translate(243 170)">
          <rect x="0.5" y="0.5" width="11" height="11" fill="none" stroke="var(--green)" stroke-width="1.4"/>
          <path d="M2.5 6 L5 8.8 L10.5 1.5" fill="none" stroke="var(--ink)" stroke-width="1.8"/>
          <text class="service" x="20" y="10.5" font-size="14">Financial Planning</text>
        </g>
        <g class="service-item" transform="translate(243 196)">
          <rect x="0.5" y="0.5" width="11" height="11" fill="none" stroke="var(--green)" stroke-width="1.4"/>
          <path d="M2.5 6 L5 8.8 L10.5 1.5" fill="none" stroke="var(--ink)" stroke-width="1.8"/>
          <text class="service" x="20" y="10.5" font-size="14">Tax Planning</text>
        </g>
        <g class="service-item" transform="translate(420 170)">
          <rect x="0.5" y="0.5" width="11" height="11" fill="none" stroke="var(--green)" stroke-width="1.4"/>
          <path d="M2.5 6 L5 8.8 L10.5 1.5" fill="none" stroke="var(--ink)" stroke-width="1.8"/>
          <text class="service" x="20" y="10.5" font-size="14">Investment Management</text>
        </g>
        <g class="service-item" transform="translate(420 196)">
          <rect x="0.5" y="0.5" width="11" height="11" fill="none" stroke="var(--green)" stroke-width="1.4"/>
          <path d="M2.5 6 L5 8.8 L10.5 1.5" fill="none" stroke="var(--ink)" stroke-width="1.8"/>
          <text class="service" x="20" y="10.5" font-size="14">Insurance</text>
        </g>
      </g>

      <!-- call to action text -->
      <text class="cta" x="30" y="263" font-size="32" textLength="199" lengthAdjust="spacingAndGlyphs">TALK TO US</text>
      <g class="phone-icon">
        <circle cx="257" cy="251" r="16" fill="var(--white)"/>
        <path d="M251 242 c-2 1 -3 3 -2 6 c1 5 6 10 11 11 c3 1 5 0 6 -2 l-1 -2 l-4 -2 l-2 2 c-3 -1 -5 -4 -6 -6 l2 -2 l-2 -4 z" fill="var(--green)"/>
      </g>
      <text class="cta" x="288" y="265" font-size="34" textLength="300" lengthAdjust="spacingAndGlyphs">302-418-2907</text>

      <!-- since badge -->
      <g class="since-badge">
        <circle cx="671" cy="211" r="51" fill="none" stroke="#008a5c" stroke-width="7" stroke-dasharray="3 2.5"/>
        <circle cx="671" cy="211" r="49" fill="url(#badgeTone)"/>
        <circle cx="671" cy="211" r="44" fill="none" stroke="rgba(255,255,255,0.25)" stroke-width="1"/>
        <text class="badge-text" x="671" y="190" font-size="11.5" text-anchor="middle">SERVING</text>
        <text class="badge-text" x="671" y="204" font-size="11.5" text-anchor="middle">THE AREA</text>
        <text class="badge-text" x="671" y="218" font-size="11.5" text-anchor="middle">SINCE</text>
        <text class="badge-year" x="671" y="246" font-size="30" text-anchor="middle">1980</text>
      </g>
    </svg>
  </section>
</main>
</body>
</html>
```